Health Care Company with Logo Needs Business Cards designed

We are a luxury behavioral health company looking for business cards design we already have a logo and are looking for someone to design a sophisticated luxurious looking business card. Please note that Card design should be captivating just like the logo and also encompass the logo color

Industry/Entity Type

Healthcare

Contact Information for Business Card

Logo,company name, tagline, my name and title, contact details, and physical address

```html
<!DOCTYPE html>
<html lang="en">
<head>
<meta charset="utf-8">
<title>Corvin Wellness Group – Business Cards</title>
<link href="https://fonts.googleapis.com/css2?family=Roboto+Condensed:wght@400;700&display=swap" rel="stylesheet">
<style>
  :root {
    --backdrop: #8e8e8e;
    --card: #1a1a1a;
    --orange: #f7931e;
    --green: #8dc63f;
    --blue: #00aeef;
    --purple: #7f3f98;
    --white: #ffffff;
    --muted: #c9c9c9;
    --font: "Roboto Condensed", sans-serif;
  }
  * { box-sizing: border-box; margin: 0; padding: 0; }
  html, body { width: 1200px; height: 588px; overflow: hidden; }
  body { background: var(--backdrop); font-family: var(--font); position: relative; }

  .card { position: absolute; background: var(--card); overflow: hidden; }
  .card--front { left: 87px; top: 141px; width: 485px; height: 287px; }
  .card--back { left: 622px; top: 143px; width: 488px; height: 286px; }

  .brand { position: absolute; display: flex; align-items: flex-start; gap: 10px; }
  .brand__square { width: 18px; height: 18px; background: var(--orange); margin-top: 4px; flex: none; }
  .brand__name { color: var(--white); font-weight: 700; line-height: 1; }
  .brand__tagline { color: var(--muted); font-weight: 400; margin-top: 6px; line-height: 1; }

  .card--front .brand { left: 27px; top: 30px; }
  .card--front .brand__name { font-size: 24px; }
  .card--front .brand__tagline { font-size: 11px; }

  .card--back .brand { left: 156px; top: 118px; }
  .card--back .brand__square { width: 22px; height: 22px; margin-top: 5px; }
  .card--back .brand__name { font-size: 30px; }
  .card--back .brand__tagline { font-size: 13px; }

  .person { position: absolute; left: 26px; top: 100px; color: var(--white); }
  .person__name { color: var(--blue); font-size: 19px; font-weight: 700; text-transform: uppercase; line-height: 1; }
  .person__title { font-size: 13px; margin-top: 6px; }

  .address { position: absolute; left: 26px; top: 154px; color: var(--white); font-size: 13px; font-style: normal; line-height: 18px; }

  .contacts { position: absolute; left: 26px; top: 211px; list-style: none; color: var(--white); font-size: 13px; line-height: 18px; }
  .contacts li { display: flex; align-items: center; gap: 6px; }
  .contacts svg { width: 10px; height: 10px; flex: none; }

  .stripes { position: absolute; top: 0; bottom: 0; display: flex; flex-direction: column; }
  .card--front .stripes { right: 0; width: 44px; }
  .card--back .stripes { left: 0; width: 60px; }
  .stripes span { flex: 1; }
  .stripe--orange { background: var(--orange); }
  .stripe--green { background: var(--green); }
  .stripe--blue { background: var(--blue); }
  .stripe--purple { background: var(--purple); }
</style>
</head>
<body>
  <section class="card card--front" aria-label="Business card front">
    <div class="brand">
      <span class="brand__square"></span>
      <div>
        <p class="brand__name">Corvin Wellness Group</p>
        <p class="brand__tagline">Compassionate care at every step</p>
      </div>
    </div>

    <div class="person">
      <p class="person__name">Daniel Reyes</p>
      <p class="person__title">President</p>
    </div>

    <address class="address">
      1830 Harbor View Drive<br>
      Laguna Cove CA 92651
    </address>

    <ul class="contacts">
      <li>
        <svg viewBox="0 0 10 10" aria-hidden="true"><path fill="var(--orange)" d="M2 0.5 L3.6 2.6 L2.7 3.6 Q3.8 5.8 6.3 7.2 L7.3 6.3 L9.5 8 L8.3 9.5 Q1 8 0.5 1.7 Z"/></svg>
        555-310-4827
      </li>
      <li>
        <svg viewBox="0 0 10 10" aria-hidden="true"><rect x="0.5" y="2" width="9" height="6.5" fill="var(--green)"/><path d="M0.5 2 L5 5.6 L9.5 2" fill="none" stroke="var(--card)" stroke-width="0.9"/></svg>
        info@corvinwellness.com
      </li>
      <li>
        <svg viewBox="0 0 10 10" aria-hidden="true"><circle cx="5" cy="5" r="4.5" fill="var(--purple)"/><path d="M0.5 5 H9.5 M5 0.5 Q2.5 5 5 9.5 M5 0.5 Q7.5 5 5 9.5" fill="none" stroke="var(--card)" stroke-width="0.6"/></svg>
        www.corvinwellness.com
      </li>
    </ul>

    <div class="stripes" aria-hidden="true">
      <span class="stripe--orange"></span>
      <span class="stripe--green"></span>
      <span class="stripe--blue"></span>
      <span class="stripe--purple"></span>
    </div>
  </section>

  <section class="card card--back" aria-label="Business card back">
    <div class="stripes" aria-hidden="true">
      <span class="stripe--orange"></span>
      <span class="stripe--green"></span>
      <span class="stripe--blue"></span>
      <span class="stripe--purple"></span>
    </div>

    <div class="brand">
      <span class="brand__square"></span>
      <div>
        <p class="brand__name">Corvin Wellness Group</p>
        <p class="brand__tagline">Compassionate care at every step</p>
      </div>
    </div>
  </section>
</body>
</html>
```